Animal Eye Clinic needs a Business card

We are a new veterinary ophthalmology practice (Ridgeline Pet Vision Care) and we need a business card designed. We only see animal eyes - we are not a regular veterinary clinic. We already have a logo. We are looking for a professional, good looking business card to hand out to our clients. We are looking for something simple but professional and contemporary. Our logo is likely the only picture/graphic that needs to be on the card.
Updates

Contact Information for Business Card

Delia Vossman, BSc, DVM, MSc, DipACVO
Veterinary Ophthalmologist

Phone: 250.418.3927
Email: ridgelinepetvisioncare@mailbox-example.net
Website: ridgelinepetvisioncare-example.net
Address: 1874 Thornbury Rd
Kelowna, BC, V1X 4M9

Colors

Designer to choose colors to be used in the design.

Requirements
Must have
• Our logo (attached)

```html
<!DOCTYPE html>
<html lang="en">
<head>
<meta charset="utf-8">
<title>Ridgeline Pet Vision Care – Business Card</title>
<link rel="stylesheet" href="https://fonts.googleapis.com/css2?family=Roboto:wght@400;500;700&display=swap">
<style>
  :root {
    --page-bg: #d9d4cc;
    --card-light: #f4f6f6;
    --card-mid: #dfe4e5;
    --brand-teal: #1d6e78;
    --band-teal: #1f6f79;
    --band-teal-deep: #13555e;
    --swoosh-dark: #35393c;
    --silver: #e8ecec;
    --text-light: #eef3f3;
    --text-soft: #cfdcdd;
    --address: #d5ddd9;
  }
  html, body {
    margin: 0;
    width: 1200px;
    height: 970px;
    overflow: hidden;
    background: var(--page-bg);
    font-family: "Roboto", Arial, sans-serif;
  }
  .business-card {
    position: absolute;
    left: 80px;
    top: 189px;
    width: 1040px;
    height: 592px;
    border-radius: 26px;
    overflow: hidden;
    background: linear-gradient(160deg, var(--card-light) 0%, var(--card-mid) 100%);
    box-shadow: 0 12px 40px rgba(0,0,0,0.18);
  }
  .card-waves {
    position: absolute;
    inset: 0;
    width: 100%;
    height: 100%;
  }
  .brand {
    position: absolute;
    left: 60px;
    top: 82px;
    display: flex;
    align-items: center;
    gap: 34px;
  }
  .brand-dot {
    width: 136px;
    height: 136px;
    border-radius: 50%;
    background: var(--brand-teal);
  }
  .brand-name {
    margin: 0;
    color: var(--brand-teal);
    font-weight: 700;
    font-size: 46px;
    line-height: 1.12;
    letter-spacing: 0.5px;
  }
  .contact-block {
    position: absolute;
    left: 57px;
    top: 365px;
    color: var(--text-light);
  }
  .person-name {
    margin: 0;
    font-size: 28px;
    font-weight: 400;
    color: var(--text-soft);
  }
  .person-name strong { font-weight: 700; color: var(--text-light); }
  .person-title {
    margin: 4px 0 0;
    font-size: 23px;
    color: var(--text-light);
  }
  .contact-list {
    list-style: none;
    margin: 26px 0 0;
    padding: 0;
    font-size: 23px;
  }
  .contact-list li {
    display: flex;
    align-items: center;
    gap: 14px;
    height: 33px;
    color: var(--text-soft);
  }
  .contact-list svg { width: 24px; height: 20px; flex: none; }
  .address {
    position: absolute;
    left: 712px;
    top: 488px;
    margin: 0;
    font-style: normal;
    font-size: 23px;
    line-height: 33px;
    color: var(--address);
  }
</style>
</head>
<body>
  <section class="business-card">
    <svg class="card-waves" viewBox="0 0 1040 592" preserveAspectRatio="none" aria-hidden="true">
      <defs>
        <linearGradient id="bandGrad" x1="0" y1="0" x2="1" y2="1">
          <stop offset="0" stop-color="#2a7b85"/>
          <stop offset="1" stop-color="#13555e"/>
        </linearGradient>
      </defs>
      <path d="M0,330 C220,290 470,318 640,350 C800,378 950,330 1040,170 L1040,352 C900,372 780,372 640,364 C430,350 230,338 0,352 Z" fill="#35393c"/>
      <path d="M0,352 C230,338 430,350 640,364 C780,372 900,372 1040,352 L1040,360 C900,380 780,380 640,372 C430,358 230,346 0,360 Z" fill="#e8ecec"/>
      <path d="M0,360 C230,346 430,358 640,372 C780,380 900,380 1040,360 L1040,592 L0,592 Z" fill="url(#bandGrad)"/>
    </svg>

    <header class="brand">
      <div class="brand-dot"></div>
      <h1 class="brand-name">RIDGELINE<br>PET VISION CARE</h1>
    </header>

    <div class="contact-block">
      <p class="person-name"><strong>Delia Vossman</strong>, BSc, DVM, MSc, DipACVO</p>
      <p class="person-title">Veterinary Ophthalmologist</p>
      <ul class="contact-list">
        <li>
          <svg viewBox="0 0 24 20" aria-hidden="true"><path d="M3 6 C3 3 6 2 12 2 C18 2 21 3 21 6 L17 8 L16 5 L8 5 L7 8 Z M6 10 L18 10 L20 18 L4 18 Z" fill="#cfdcdd"/></svg>
          250.418.3927
        </li>
        <li>
          <svg viewBox="0 0 24 20" aria-hidden="true"><rect x="2" y="3" width="20" height="14" fill="#cfdcdd"/><path d="M2 3 L12 11 L22 3" fill="none" stroke="#1f6f79" stroke-width="1.6"/></svg>
          ridgelinepetvisioncare@mailbox-example.net
        </li>
        <li>
          <svg viewBox="0 0 24 20" aria-hidden="true"><g fill="none" stroke="#cfdcdd" stroke-width="1.6"><circle cx="12" cy="10" r="8"/><ellipse cx="12" cy="10" rx="3.5" ry="8"/><path d="M4 10 H20 M5.5 6 H18.5 M5.5 14 H18.5"/></g></svg>
          ridgelinepetvisioncare-example.net
        </li>
      </ul>
    </div>

    <address class="address">1874 Thornbury Rd<br>Kelowna, BC, V1X 4M9</address>
  </section>
</body>
</html>
```